Business Card Design

Looking for business card designs for a new business. there will be two cards of the same design (both lots of information below in contact info). We would like the logo diagonally across the card with the information split above and below the logo similar to sketch. happy to look at similar alternatives
Please use same colours as in logo design

Industry/Entity Type

Business

Contact Information for Business Card

Dwight Halloran
mob - 0491 738 204
ph - 02 6148 3920
fax - 02 6148 3975
email - dwight@kestrelbeams.com.au
14 Larkmoor Road, Taminda NSW 2340

Colin Marchetti
mob - 0438 912 557
ph - 02 6148 3920
fax - 02 6148 3975
email - colin@kestrelbeams.com.au

```html
<!DOCTYPE html>
<html lang="en">
<head>
<meta charset="utf-8">
<title>Kestrel Beams – Business Cards</title>
<link rel="stylesheet" href="https://fonts.googleapis.com/css2?family=Open+Sans:wght@400;600;700&display=swap">
<style>
  :root {
    --teal: #0b7d77;
    --ink: #111111;
    --paper: #ffffff;
    --backdrop: #e9e7e3;
    --text: #222222;
  }
  * { margin: 0; padding: 0; box-sizing: border-box; }
  html, body {
    width: 1144px;
    height: 1200px;
    overflow: hidden;
    background: var(--backdrop);
    font-family: "Open Sans", Arial, sans-serif;
  }
  .card {
    position: absolute;
    overflow: hidden;
    box-shadow: 0 2px 6px rgba(0,0,0,0.25);
  }
  /* Front card */
  .card--front {
    left: 168px; top: 28px;
    width: 942px; height: 541px;
    background: var(--paper);
    border: 1px solid #444;
  }
  .wordmark {
    position: absolute;
    left: 0; right: 0;
    text-align: center;
    font-weight: 700;
    color: var(--ink);
    letter-spacing: 1px;
    white-space: nowrap;
  }
  .card--front .wordmark { top: 58px; font-size: 76px; line-height: 1; }
  .wordmark-square {
    display: inline-block;
    width: 0.62em; height: 0.62em;
    background: var(--teal);
    margin-right: 0.22em;
    vertical-align: 0.02em;
  }
  .holder-name {
    position: absolute;
    top: 236px; left: 0; right: 0;
    text-align: center;
    font-size: 30px;
    font-weight: 600;
    color: var(--teal);
  }
  .contact-line {
    position: absolute;
    left: 0; right: 0;
    text-align: center;
    font-size: 22px;
    color: var(--text);
    white-space: nowrap;
  }
  .contact-line--phones { top: 314px; }
  .contact-line--email { top: 358px; }
  .contact-item { display: inline-flex; align-items: center; gap: 5px; margin: 0 4px; }
  .contact-icon { width: 18px; height: 18px; fill: var(--teal); }
  .card-wave {
    position: absolute;
    left: 0; top: 0;
    width: 942px; height: 541px;
  }
  .address {
    position: absolute;
    top: 496px; left: 0; right: 0;
    text-align: center;
    font-size: 22px;
    color: var(--paper);
  }
  /* Back card */
  .card--back {
    left: 28px; top: 626px;
    width: 943px; height: 536px;
    background: var(--teal);
  }
  .card--back .wordmark {
    top: 198px;
    font-size: 92px;
    line-height: 1;
  }
  .card--back .wordmark-square { background: var(--ink); }
  .website {
    position: absolute;
    top: 422px; left: 0; right: 0;
    text-align: center;
    font-size: 29px;
    color: var(--paper);
    letter-spacing: 3px;
  }
  .website strong { font-weight: 600; }
</style>
</head>
<body>

<section class="card card--front">
  <svg class="card-wave" viewBox="0 0 942 541" aria-hidden="true">
    <path d="M0,454 C120,470 200,478 330,462 C430,449 520,438 620,446 C760,458 870,480 942,492 L942,541 L0,541 Z" fill="var(--teal)"/>
    <path d="M0,428 C90,455 180,470 300,452 C420,434 520,422 620,432 C760,446 870,470 942,486 L942,492 C860,476 760,456 620,444 C520,436 420,446 300,462 C180,478 90,462 0,442 Z" fill="var(--ink)"/>
  </svg>

  <div class="wordmark"><span class="wordmark-square"></span>Kestrel Beams</div>

  <h1 class="holder-name">Colin Marchetti</h1>

  <p class="contact-line contact-line--phones">
    <span class="contact-item">
      <svg class="contact-icon" viewBox="0 0 24 24" aria-label="Phone"><path d="M6.6 10.8a15.1 15.1 0 0 0 6.6 6.6l2.2-2.2a1 1 0 0 1 1-.25 11.4 11.4 0 0 0 3.6.57 1 1 0 0 1 1 1V20a1 1 0 0 1-1 1A17 17 0 0 1 3 4a1 1 0 0 1 1-1h3.5a1 1 0 0 1 1 1c0 1.25.2 2.450.57 3.57a1 1 0 0 1-.25 1z"/></svg>02 6148 3920
    </span>
    <span class="contact-item">
      <svg class="contact-icon" viewBox="0 0 24 24" aria-label="Mobile"><path d="M7 1h10a2 2 0 0 1 2 2v18a2 2 0 0 1-2 2H7a2 2 0 0 1-2-2V3a2 2 0 0 1 2-2zm0 3v13h10V4zm5 15a1.2 1.2 0 1 0 0 2.4A1.2 1.2 0 0 0 12 19z"/></svg>0438 912 557
    </span>
    <span class="contact-item">
      <svg class="contact-icon" viewBox="0 0 24 24" aria-label="Fax"><path d="M6 2h9l3 3v5H6zM3 11h18a1 1 0 0 1 1 1v8a1 1 0 0 1-1 1H3a1 1 0 0 1-1-1v-8a1 1 0 0 1 1-1zm3 3v2h4v-2zm8 0v2h4v-2z"/></svg>02 6148 3975
    </span>
  </p>

  <p class="contact-line contact-line--email">
    <span class="contact-item">
      <svg class="contact-icon" viewBox="0 0 24 24" aria-label="Email"><path d="M2 9l10-6 10 6v11a1 1 0 0 1-1 1H3a1 1 0 0 1-1-1zm2 1.2V12l8 5 8-5v-1.8l-8 5z"/></svg>colin@kestrelbeams.com.au
    </span>
  </p>

  <p class="address">14 Larkmoor Road, Brackenvale NSW 2361</p>
</section>

<section class="card card--back">
  <div class="wordmark"><span class="wordmark-square"></span>Kestrel Beams</div>
  <p class="website">www.<strong>kestrelbeams</strong>.com.au</p>
</section>

</body>
</html>
```